Business card design for my company.
I would like the card's background colour to be black. You can also see our web site to get an idea of our brand. https://www.tmwhomecrafting.com.au/
- Name
- Email

```html
<!DOCTYPE html>
<html lang="en">
<head>
<meta charset="utf-8">
<title>TMW Home Crafting – Business Card</title>
<link rel="stylesheet" href="https://fonts.googleapis.com/css2?family=Montserrat:wght@400;700&display=swap">
<style>
  :root {
    --stage: #2a2a2a;
    --card: #1f1f1f;
    --green: #1f9a48;
    --white: #f2f2f2;
    --muted: #d9d9d9;
  }
  * { box-sizing: border-box; margin: 0; padding: 0; }
  html, body {
    width: 1200px;
    height: 801px;
    overflow: hidden;
    background: var(--stage);
    font-family: "Montserrat", sans-serif;
  }
  .stage {
    width: 1200px;
    height: 801px;
    display: flex;
    align-items: center;
    justify-content: center;
    gap: 40px;
  }
  .card {
    width: 520px;
    height: 297px;
    background: var(--card);
    border-radius: 16px;
    position: relative;
    box-shadow: 0 10px 30px rgba(0,0,0,0.45);
  }
  /* Front: brand name + contact details */
  .card--front {
    display: flex;
    align-items: center;
  }
  .brand {
    display: flex;
    align-items: center;
    gap: 10px;
    color: var(--white);
    font-weight: 700;
    text-transform: uppercase;
    letter-spacing: 1.5px;
  }
  .brand__dot {
    width: 12px;
    height: 12px;
    background: var(--green);
    flex: none;
  }
  .card--front .brand {
    width: 230px;
    padding-left: 34px;
    font-size: 17px;
    line-height: 1.3;
  }
  .divider {
    width: 1px;
    height: 120px;
    background: var(--green);
    margin-right: 26px;
  }
  .contact__name {
    color: var(--green);
    font-weight: 700;
    font-size: 20px;
    letter-spacing: 0.5px;
    text-transform: uppercase;
  }
  .contact__role {
    color: var(--muted);
    font-size: 12px;
    margin: 2px 0 18px;
  }
  .contact__list { list-style: none; }
  .contact__item {
    display: flex;
    align-items: center;
    gap: 8px;
    color: var(--white);
    font-size: 11.5px;
    margin-bottom: 6px;
  }
  .contact__icon { width: 11px; height: 11px; flex: none; }
  /* Back: brand name only */
  .card--back {
    display: flex;
    align-items: center;
    justify-content: center;
  }
  .card--back .brand {
    font-size: 28px;
    letter-spacing: 3px;
    gap: 14px;
  }
  .card--back .brand__dot { width: 18px; height: 18px; }
</style>
</head>
<body>
<main class="stage">
  <section class="card card--front">
    <div class="brand">
      <span class="brand__dot"></span>
      <span>TMW Home Crafting</span>
    </div>
    <div class="divider"></div>
    <div class="contact">
      <h1 class="contact__name">Darren Hollis</h1>
      <p class="contact__role">CEO/Founder</p>
      <ul class="contact__list">
        <li class="contact__item">
          <svg class="contact__icon" viewBox="0 0 24 24" aria-hidden="true"><path fill="#1f9a48" d="M6.6 10.8a15.1 15.1 0 0 0 6.6 6.6l2.2-2.2a1 1 0 0 1 1-.25 11.4 11.4 0 0 0 3.6.57 1 1 0 0 1 1 1V20a1 1 0 0 1-1 1A17 17 0 0 1 3 4a1 1 0 0 1 1-1h3.5a1 1 0 0 1 1 1c0 1.25.2 2.45.57 3.57a1 1 0 0 1-.25 1z"/></svg>
          415-220-7391
        </li>
        <li class="contact__item">
          <svg class="contact__icon" viewBox="0 0 24 24" aria-hidden="true"><path fill="#1f9a48" d="M2 5h20v14H2z"/><path fill="none" stroke="#1f1f1f" stroke-width="2" d="M2 5l10 8 10-8"/></svg>
          info@tmwhomecrafting.com.au
        </li>
        <li class="contact__item">
          <svg class="contact__icon" viewBox="0 0 24 24" aria-hidden="true"><circle cx="12" cy="12" r="10" fill="#1f9a48"/><path fill="none" stroke="#1f1f1f" stroke-width="1.5" d="M2 12h20M12 2c3 3 3 17 0 20M12 2c-3 3-3 17 0 20"/></svg>
          www.tmwhomecrafting.com.au
        </li>
      </ul>
    </div>
  </section>
  <section class="card card--back">
    <div class="brand">
      <span class="brand__dot"></span>
      <span>TMW Home Crafting</span>
    </div>
  </section>
</main>
</body>
</html>
```